Visitenkarten-Design für Garten- und Landschaftspflege
Nerapo Kulm setzte meine Vorstellungen absolut super um ich kann Ihn nur weiter empfehlen. vielen dank
Zielgruppe
Baumpflege, Baumfällung, Garten und Landschaftspflege meine zielgruppe sind Privatpersonen im alter von 20-100Jahren
Aufgabenstellung
Sehr geehrte Damen und Herren, die visitenkarte sollte die angaben so enthalten wie sie auf der von mir gestallteten Visitenkarten sind ( meine ist kein maß der Dinge). Ich habe mein Logo leider nur als 3.jpg Datei. Das Logo darf im Design erändert werden aber bitte nur Feinheiten ansonsten stehen ihnen alle türen offen um kreativ zu sein.
mit freundlichen Grüßen Jonas Vehmar

```html
<!DOCTYPE html>
<html lang="de">
<head>
<meta charset="utf-8">
<title>Visitenkarte Baumpflege Vehmar</title>
<link rel="stylesheet" href="https://fonts.googleapis.com/css2?family=Fira+Sans:wght@400;500;600;700&display=swap">
<style>
  :root {
    --page: #ffffff;
    --leaf-light: #9ebd3e;
    --leaf-dark: #8aa83a;
    --ink: #101010;
    --shadow: rgba(0, 0, 0, 0.22);
  }
  * { margin: 0; padding: 0; box-sizing: border-box; }
  html, body {
    width: 1200px; height: 840px; overflow: hidden;
    background: var(--page);
    font-family: "Fira Sans", Arial, sans-serif;
    color: var(--ink);
  }
  .canvas { position: relative; width: 1200px; height: 840px; }
  .card {
    position: absolute; top: 152px;
    width: 334px; height: 516px;
    background: var(--leaf-light);
    box-shadow: 5px 5px 6px var(--shadow);
    overflow: hidden;
  }
  .card--front { left: 224px; }
  .card--back { left: 635px; }
  .card__texture { position: absolute; inset: 0; }
  .card--front .card__texture {
    background: linear-gradient(180deg, var(--leaf-light) 0%, var(--leaf-light) 10%, var(--leaf-dark) 16%, var(--leaf-dark) 45%, var(--leaf-light) 70%, var(--leaf-light) 94%, var(--leaf-dark) 100%);
  }
  .card--back .card__texture {
    background: linear-gradient(180deg, var(--leaf-light) 0%, var(--leaf-light) 10%, var(--leaf-dark) 16%, var(--leaf-dark) 96%, var(--leaf-light) 100%);
  }
  .card__content { position: absolute; inset: 0; }

  .brand-mark {
    position: absolute; border-radius: 50%; background: var(--ink);
  }
  .card--front .brand-mark { left: 132px; top: 52px; width: 70px; height: 70px; }
  .card--back .brand-mark { left: 84px; top: 45px; width: 34px; height: 34px; }

  .brand-name {
    position: absolute; left: 31px;
    font-weight: 700; text-transform: uppercase; white-space: nowrap;
    color: var(--ink);
  }
  .card--front .brand-name {
    top: 160px; font-size: 19px; letter-spacing: 0.21em; line-height: 30px;
  }
  .card--back .brand-name {
    top: 101px; font-size: 10px; letter-spacing: 0.26em; line-height: 16px;
  }
  .brand-rule { position: absolute; left: 32px; background: var(--ink); }
  .card--front .brand-rule { top: 193px; width: 270px; height: 2.5px; }
  .card--back .brand-rule { top: 119px; width: 141px; height: 1.5px; }

  .contact { position: absolute; left: 30px; top: 259px; font-size: 17.5px; line-height: 23.5px; font-weight: 500; }
  .contact p { white-space: nowrap; }
  .contact__name { font-weight: 600; }
  .contact__gap { height: 24px; }

  .services__title {
    position: absolute; left: 31px; top: 157px;
    font-size: 21px; font-weight: 700; letter-spacing: 0.18em; line-height: 30px;
    text-transform: uppercase; white-space: nowrap;
  }
  .rule { position: absolute; left: 31px; width: 253px; height: 2.5px; background: var(--ink); }
  .rule--top { top: 191px; }
  .rule--bottom { top: 424px; }
  .services__list {
    position: absolute; left: 30px; top: 200px;
    list-style: none; font-size: 18px; font-weight: 500; line-height: 21.4px;
  }
  .services__list li { position: relative; padding-left: 11px; white-space: nowrap; }
  .services__list li::before { content: "•"; position: absolute; left: 0; }
  .services__extra {
    position: absolute; left: 31px; top: 436px;
    font-size: 17px; font-weight: 500; line-height: 21px;
  }
</style>
</head>
<body>
<main class="canvas">
  <section class="card card--front">
    <div class="card__texture" role="img" aria-label="Faint tree silhouette texture in two shades of green"></div>
    <div class="card__content">
      <div class="brand-mark" aria-hidden="true"></div>
      <p class="brand-name">Baumpflege Vehmar</p>
      <div class="brand-rule"></div>
      <div class="contact">
        <p class="contact__name">Jonas Vehmar</p>
        <p>Fachagrarwirt</p>
        <p>Baumpflege/Baumsanierung</p>
        <div class="contact__gap"></div>
        <p>Lindenweg 7</p>
        <p>85600 Birkenau</p>
        <p>0172 48291053</p>
        <p>www.baumpflege-vehmar.de</p>
        <p>kontakt@baumpflege-vehmar.de</p>
      </div>
    </div>
  </section>

  <section class="card card--back">
    <div class="card__texture" role="img" aria-label="Faint tree silhouette texture in two shades of green"></div>
    <div class="card__content">
      <div class="brand-mark" aria-hidden="true"></div>
      <p class="brand-name">Baumpflege Vehmar</p>
      <div class="brand-rule"></div>
      <h2 class="services__title">Unsere Leistungen</h2>
      <div class="rule rule--top"></div>
      <ul class="services__list">
        <li>Neupflanzungen</li>
        <li>Herstellen der<br>Verkehrssicherheit von Bäumen</li>
        <li>Kronenrückschnitt<br>(Einkürzung &amp; Kronenpflege)</li>
        <li>Prüfen von Bäumen auf<br>Standsicherheit</li>
        <li>Fällung von Bäumen</li>
        <li>Obstbaumschnitt</li>
        <li>Fräsen von Wurzelstöcken</li>
      </ul>
      <div class="rule rule--bottom"></div>
      <p class="services__extra">Aufbau &amp; Anfertigung von<br>Gartenhäusern nach Maß</p>
    </div>
  </section>
</main>
</body>
</html>
```